Laser Tattoo Removal Business Cards

We are looking for a professional business card design for a laser tattoo removal business. Ideally looking for a black business card design. The name of the business is Brightline Tattoo Removal. We place our cards at local tattoo shops so we ideally are looking for something trendy/edgy to draw both male and female clientele in.

Target Market(s)

Male/Female ages 18-60

Contact Information for Business Card

black background ideally.. hoping to stay within greys, whites and black

Font styles to use
Serif
Sans Serif

Colors
121212
a9a9a9
5c5c5c
f5f5f5
ffffff
7f7f7f
606060
848484
9d9d9d

Requirements
Must have
• Employee Info:
• Melissa Thornbury
• Chief Executive Offer
• m: 919.537.2846
• w: 919.362.4178
• f: 919.685.3907
• mthornbury@brightlinetattooremoval.example
• Address:
• 4615 Oakmere Pkwy, Suite 210
• Raleigh, NC 27654
• Website:
• www.brightlinetattooremoval.example
Nice to have
• Myabe business name on back or logo on back and employee info on the front

```html
<!DOCTYPE html>
<html lang="en">
<head>
<meta charset="utf-8">
<title>Brightline Tattoo Removal – Business Card</title>
<link href="https://fonts.googleapis.com/css2?family=Roboto:wght@400&family=Roboto+Condensed:wght@500;700&display=swap" rel="stylesheet">
<style>
  :root {
    --ink: #121212;
    --ink-soft: #2a2a2a;
    --grey-mid: #5c5c5c;
    --grey: #7f7f7f;
    --grey-light: #a9a9a9;
    --paper: #f5f5f5;
    --white: #ffffff;
    --backdrop: #d6d6d6;
  }
  * { margin: 0; padding: 0; box-sizing: border-box; }
  html, body { width: 1200px; height: 960px; overflow: hidden; }
  body {
    background: var(--backdrop);
    position: relative;
    font-family: "Roboto", Arial, sans-serif;
  }
  .card {
    position: absolute;
    left: 313px;
    width: 600px;
    height: 344px;
    overflow: hidden;
  }
  .card--front { top: 113px; background: var(--paper); }
  .card--back { top: 472px; background: var(--ink); }

  .card__swoosh { position: absolute; inset: 0; width: 600px; height: 344px; }

  .brand {
    position: absolute;
    font-family: "Roboto Condensed", "Arial Narrow", sans-serif;
    font-weight: 500;
    text-transform: uppercase;
    text-align: center;
    letter-spacing: 2px;
    line-height: 1.2;
  }
  .card--front .brand { left: 42px; top: 80px; width: 200px; color: var(--ink-soft); }
  .card--back .brand { left: 362px; top: 212px; width: 210px; color: var(--white); }
  .brand__name { display: block; font-size: 34px; letter-spacing: 3px; }
  .brand__sub { display: block; font-size: 15px; letter-spacing: 3px; margin-top: 4px; }

  .person { position: absolute; left: 47px; top: 242px; width: 240px; }
  .person__name {
    font-family: "Roboto Condensed", "Arial Narrow", sans-serif;
    font-weight: 700;
    font-size: 20px;
    color: var(--ink-soft);
    letter-spacing: 0.2px;
    white-space: nowrap;
  }
  .person__title { font-size: 15px; color: var(--grey); margin-top: 1px; white-space: nowrap; }
  .person__rule { width: 23px; height: 1px; background: var(--ink-soft); margin-top: 5px; }
  .person__email {
    font-size: 11.2px;
    letter-spacing: -0.1px;
    color: var(--ink-soft);
    margin-top: 6px;
    white-space: nowrap;
  }

  .contact { position: absolute; left: 304px; top: 188px; color: var(--ink-soft); font-size: 14.5px; }
  .contact__address { line-height: 18px; color: var(--grey-mid); margin-bottom: 8px; white-space: nowrap; }
  .contact__list { list-style: none; }
  .contact__item { display: flex; align-items: center; height: 19px; white-space: nowrap; }
  .contact__item--web { font-size: 12.4px; letter-spacing: -0.1px; }
  .contact__icon { width: 12px; height: 12px; margin-right: 10px; fill: var(--ink-soft); flex: none; }
</style>
</head>
<body>

<section class="card card--front" aria-label="Card front">
  <svg class="card__swoosh" viewBox="0 0 600 344" aria-hidden="true">
    <path d="M525 0 Q585 140 590 344 L600 344 L600 0 Z" fill="var(--ink)"/>
    <path d="M512 0 Q568 140 578 344 L590 344 Q585 140 525 0 Z" fill="var(--paper)"/>
    <path d="M510 0 Q555 120 568 300 Q570 200 522 0 Z" fill="var(--grey-light)"/>
  </svg>

  <div class="brand">
    <span class="brand__name">Brightline</span>
    <span class="brand__sub">Tattoo Removal</span>
  </div>

  <div class="person">
    <div class="person__name">MELISSA THORNBURY</div>
    <div class="person__title">Chief Executive Offer</div>
    <div class="person__rule"></div>
    <div class="person__email">mthornbury@brightlinetattooremoval.example</div>
  </div>

  <div class="contact">
    <p class="contact__address">4615 Oakmere Pkwy, Suite 210<br>Raleigh, NC 27654</p>
    <ul class="contact__list">
      <li class="contact__item">
        <svg class="contact__icon" viewBox="0 0 12 12" aria-label="Work phone"><path d="M2.5 0.5 L4.5 3 L3.3 4.3 Q4.5 6.8 7.7 8.7 L9 7.5 L11.5 9.5 L10.2 11.3 Q5 11 0.7 2 Z"/></svg>
        <span>919.362.4178</span>
      </li>
      <li class="contact__item">
        <svg class="contact__icon" viewBox="0 0 12 12" aria-label="Mobile"><path d="M3 0 H9 V12 H3 Z M4 1.5 V9.5 H8 V1.5 Z M5.4 10.2 H6.6 V11.2 H5.4 Z"/></svg>
        <span>919.537.2846</span>
      </li>
      <li class="contact__item">
        <svg class="contact__icon" viewBox="0 0 12 12" aria-label="Fax"><path d="M3 0 H9 V3.5 H3 Z M0.5 4.5 H11.5 V9.5 H9.5 V12 H2.5 V9.5 H0.5 Z M3.5 8 V11 H8.5 V8 Z"/></svg>
        <span>919.685.3907</span>
      </li>
      <li class="contact__item contact__item--web">
        <svg class="contact__icon" viewBox="0 0 12 12" aria-label="Website"><circle cx="6" cy="6" r="5.8"/><path d="M3 3.5 Q5 2.5 5.5 5 Q4 6 4.5 8.5 Q2.5 7 3 3.5 Z M7 7 Q9 6.5 9.5 8.5 Q8 10 7 9 Z" fill="var(--paper)"/></svg>
        <span>www.brightlinetattooremoval.example</span>
      </li>
    </ul>
  </div>
</section>

<section class="card card--back" aria-label="Card back">
  <div class="brand">
    <span class="brand__name">Brightline</span>
    <span class="brand__sub">Tattoo Removal</span>
  </div>
</section>

</body>
</html>
```